Business Card Design

Lintel PR is a public relations consultancy service for the self build, home refurbishment and home improvement market.
It represents everything about 'home' so envisage logo featuring maybe roof pitch over the 'A' of Lintel. Colour/font undecided.

Industry/Entity Type

Home Improvement

Contact Information for Business Card

Fenna Corrowdale
fenna@lintelpr-mail.co.uk
Telephone Direct: 0712 645 8219

```html
<!DOCTYPE html>
<html lang="en">
<head>
<meta charset="utf-8">
<title>Lintel PR – Business Card</title>
<link href="https://fonts.googleapis.com/css2?family=Exo+2:wght@400;600;800&display=swap" rel="stylesheet">
<style>
  :root {
    --stage: #6b6b6b;
    --paper: #f4f4f4;
    --charcoal: #3a3a3a;
    --slate: #9a9a9a;
    --orange: #e98a0c;
    --orange-deep: #d96f05;
    --amber: #f6b40c;
    --ink: #2e2e2e;
  }
  * { box-sizing: border-box; margin: 0; padding: 0; }
  html, body { width: 1200px; height: 750px; overflow: hidden; }
  body {
    background: var(--stage);
    font-family: "Exo 2", sans-serif;
    display: flex;
    align-items: center;
    justify-content: center;
    gap: 40px;
  }
  .card {
    position: relative;
    width: 520px;
    height: 297px;
    background: var(--paper);
    overflow: hidden;
    box-shadow: 0 10px 30px rgba(0,0,0,.35);
  }
  .card svg.card-art { position: absolute; inset: 0; }

  .brand { position: absolute; display: flex; align-items: center; gap: 12px; }
  .brand-square { background: var(--charcoal); }
  .brand-name { font-weight: 800; color: var(--ink); letter-spacing: .02em; text-transform: uppercase; }

  .card-front .brand { left: 70px; top: 92px; }
  .card-front .brand-square { width: 58px; height: 58px; }
  .card-front .brand-name { font-size: 42px; }
  .front-web {
    position: absolute; right: 22px; top: 190px;
    font-size: 11px; letter-spacing: .18em; color: var(--charcoal);
  }

  .card-back .brand { right: 40px; top: 50px; flex-direction: column; gap: 8px; align-items: center; }
  .card-back .brand-square { width: 70px; height: 56px; }
  .card-back .brand-name { font-size: 26px; }

  .holder { position: absolute; left: 30px; top: 62px; color: var(--ink); }
  .holder-name { font-size: 18px; font-weight: 600; letter-spacing: .04em; text-transform: uppercase; }
  .holder-role { font-size: 13px; }

  .contact-list { position: absolute; left: 30px; bottom: 18px; list-style: none; }
  .contact-list li {
    display: flex; align-items: center; gap: 8px;
    font-size: 11px; color: var(--ink); line-height: 19px; letter-spacing: .03em;
  }
  .contact-list svg { width: 12px; height: 12px; flex: none; }
</style>
</head>
<body>

  <section class="card card-front" aria-label="Card front">
    <svg class="card-art" viewBox="0 0 520 297" aria-hidden="true">
      <defs>
        <linearGradient id="band-glow" x1="0" x2="1">
          <stop offset="0" stop-color="var(--orange-deep)"/>
          <stop offset=".6" stop-color="var(--amber)"/>
          <stop offset="1" stop-color="var(--orange-deep)"/>
        </linearGradient>
      </defs>
      <circle cx="560" cy="20" r="150" fill="var(--charcoal)"/>
      <rect x="0" y="176" width="520" height="32" fill="url(#band-glow)" opacity=".55"/>
      <rect x="0" y="208" width="520" height="4" fill="var(--charcoal)"/>
      <rect x="0" y="212" width="520" height="36" fill="url(#band-glow)"/>
    </svg>
    <div class="brand">
      <span class="brand-square"></span>
      <span class="brand-name">Lintel PR</span>
    </div>
    <p class="front-web">www.lintelpr-site.co.uk</p>
  </section>

  <section class="card card-back" aria-label="Card back">
    <svg class="card-art" viewBox="0 0 520 297" aria-hidden="true">
      <defs>
        <linearGradient id="panel-fill" x1="0" y1="0" x2=".6" y2="1">
          <stop offset="0" stop-color="var(--amber)"/>
          <stop offset="1" stop-color="var(--orange)"/>
        </linearGradient>
      </defs>
      <path d="M0 0 H290 Q300 120 520 190 V297 H0 Z" fill="var(--charcoal)"/>
      <path d="M0 0 H262 Q290 150 520 215 V297 H0 Z" fill="var(--slate)"/>
      <path d="M0 0 H240 Q270 160 520 232 V297 H0 Z" fill="url(#panel-fill)"/>
    </svg>

    <div class="holder">
      <p class="holder-name">Fenna Corrowdale</p>
      <p class="holder-role">Managing Director</p>
    </div>

    <ul class="contact-list">
      <li><svg viewBox="0 0 12 12"><circle cx="6" cy="6" r="6" fill="var(--ink)"/><path d="M4 3.2 5 5 4.6 5.6Q5.4 7 6.4 7.4L7 7 8.8 8 8 9Q5 9 3 4Z" fill="var(--amber)"/></svg>0712 645 8219</li>
      <li><svg viewBox="0 0 12 12"><circle cx="6" cy="6" r="6" fill="var(--ink)"/><path d="M4 3.2 5 5 4.6 5.6Q5.4 7 6.4 7.4L7 7 8.8 8 8 9Q5 9 3 4Z" fill="var(--amber)"/></svg>0712 645 8220</li>
      <li><svg viewBox="0 0 12 12"><circle cx="6" cy="6" r="6" fill="var(--ink)"/><rect x="3" y="4" width="6" height="4" fill="none" stroke="var(--amber)" stroke-width=".9"/><path d="M3 4 6 6.3 9 4" fill="none" stroke="var(--amber)" stroke-width=".9"/></svg>fenna@lintelpr-mail.co.uk</li>
      <li><svg viewBox="0 0 12 12"><circle cx="6" cy="6" r="6" fill="var(--ink)"/><circle cx="6" cy="6" r="3" fill="none" stroke="var(--amber)" stroke-width=".9"/><path d="M3 6H9M6 3V9" stroke="var(--amber)" stroke-width=".7"/></svg>www.lintelpr-site.co.uk</li>
      <li><svg viewBox="0 0 12 12"><circle cx="6" cy="6" r="6" fill="var(--ink)"/><path d="M6 9.5 3.8 6A2.3 2.3 0 1 1 8.2 6Z" fill="var(--amber)"/><circle cx="6" cy="5.2" r=".8" fill="var(--ink)"/></svg>14 Eaves Court Harrow Lane Road LK6</li>
    </ul>

    <div class="brand">
      <span class="brand-square"></span>
      <span class="brand-name">Lintel PR</span>
    </div>
  </section>

</body>
</html>
```